design a construction company business card

Design business card around our logo. Card must have all the typical info: name, title, address, phone, email, business name, etc. Somewhere on the card I would like to see our motto "Rooted in quality... Driven by dedication." Consider adding a splash of bright orange to the card to complement the blues and silvers/grays in the logo. We are open to metallic inks, textures, etc. We would like to see options on both light and dark backgrounds. The font in the logo is Euro Technic Extended Regular.

```html
<!DOCTYPE html>
<html lang="en">
<head>
<meta charset="utf-8">
<title>Halden Contracting – Business Card</title>
<link rel="stylesheet" href="https://fonts.googleapis.com/css2?family=Roboto:ital,wght@0,400;0,500;0,700;1,400&display=swap">
<style>
  :root {
    --page-bg: #e6e6e6;
    --card-white: #ffffff;
    --navy: #25409a;
    --blue: #1d6fc0;
    --royal: #2a45a8;
    --gray: #6d6e71;
    --text-dark: #4a4a4a;
    --white: #ffffff;
  }
  * { box-sizing: border-box; margin: 0; padding: 0; }
  html, body {
    width: 1125px;
    height: 1200px;
    overflow: hidden;
    background: var(--page-bg);
    font-family: "Roboto", Arial, sans-serif;
  }
  .card {
    position: absolute;
    left: 172px;
    width: 826px;
    height: 472px;
    overflow: hidden;
  }
  .card-front { top: 106px; background: var(--card-white); }
  .card-back {
    top: 640px;
    background: radial-gradient(ellipse at 55% 38%, #1b74c4 0%, #2150a8 45%, var(--royal) 85%);
  }

  /* front */
  .brand-front {
    position: absolute;
    right: 58px;
    top: 52px;
    font-weight: 700;
    font-size: 30px;
    letter-spacing: 1px;
    color: var(--navy);
    text-transform: uppercase;
    display: flex;
    align-items: center;
    gap: 12px;
  }
  .brand-square {
    width: 26px;
    height: 26px;
    background: var(--blue);
  }
  .person {
    position: absolute;
    left: 46px;
    top: 202px;
  }
  .person-name {
    font-weight: 700;
    font-size: 28px;
    color: var(--navy);
    letter-spacing: 0.3px;
  }
  .person-title {
    font-weight: 700;
    font-size: 19px;
    color: var(--gray);
    margin-top: 2px;
    letter-spacing: 0.5px;
  }
  .address {
    position: absolute;
    left: 49px;
    top: 288px;
    font-style: normal;
    font-size: 18.5px;
    line-height: 25px;
    color: var(--text-dark);
    letter-spacing: 0.4px;
  }
  .contacts {
    position: absolute;
    left: 49px;
    top: 350px;
    list-style: none;
    font-size: 18px;
    color: var(--text-dark);
    letter-spacing: 0.3px;
  }
  .contacts li {
    display: flex;
    align-items: center;
    gap: 12px;
    height: 26px;
  }
  .contacts svg { width: 18px; height: 18px; fill: var(--navy); }
  .front-band {
    position: absolute;
    left: 0;
    bottom: 0;
    width: 100%;
    height: 8px;
    background: var(--navy);
  }

  /* back */
  .brand-back {
    position: absolute;
    left: 0;
    right: 0;
    top: 222px;
    text-align: center;
  }
  .brand-back-rule {
    width: 376px;
    height: 3px;
    background: var(--white);
    margin: 0 auto 22px;
  }
  .brand-back-name {
    font-weight: 700;
    font-size: 46px;
    letter-spacing: 2px;
    color: var(--white);
    text-transform: uppercase;
    line-height: 1.1;
  }
  .motto {
    margin-top: 34px;
    font-style: italic;
    font-size: 20px;
    color: var(--white);
    letter-spacing: 0.2px;
  }
</style>
</head>
<body>
  <section class="card card-front" aria-label="Business card front">
    <div class="brand-front">
      <span class="brand-square" aria-hidden="true"></span>
      <span>Halden Contracting, Inc.</span>
    </div>

    <div class="person">
      <div class="person-name">MARCUS REED</div>
      <div class="person-title">CEO/FOUNDER</div>
    </div>

    <address class="address">
      2140 Ridgeview Court<br>
      Fairbanks, Alaska 99712
    </address>

    <ul class="contacts">
      <li>
        <svg viewBox="0 0 24 24" aria-hidden="true"><path d="M6.6 10.8a15.1 15.1 0 0 0 6.6 6.6l2.2-2.2c.3-.3.7-.4 1-.2 1.1.4 2.3.6 3.6.6.6 0 1 .4 1 1V20c0 .6-.4 1-1 1A17 17 0 0 1 3 4c0-.6.4-1 1-1h3.5c.6 0 1 .4 1 1 0 1.3.2 2.5.6 3.6.1.3 0 .7-.2 1z"/></svg>
        <span>907 555 0148</span>
      </li>
      <li>
        <svg viewBox="0 0 24 24" aria-hidden="true"><path d="M2 5h20v14H2z M4 7v.4l8 5.2 8-5.2V7z" fill-rule="evenodd"/></svg>
        <span>marcus@haldenbuild.com</span>
      </li>
      <li>
        <svg viewBox="0 0 24 24" aria-hidden="true"><circle cx="12" cy="12" r="10"/><path d="M7 8c2 0 3 1 3 3s-2 2-2 4M14 4c0 2 2 3 4 3M15 20c0-2 1-4 3-4" stroke="#fff" stroke-width="1.6" fill="none"/></svg>
        <span>www.haldenbuild.com</span>
      </li>
    </ul>

    <div class="front-band"></div>
  </section>

  <section class="card card-back" aria-label="Business card back">
    <div class="brand-back">
      <div class="brand-back-rule"></div>
      <div class="brand-back-name">Halden Contracting, Inc.</div>
      <p class="motto">Rooted in quality... Driven by dedication.</p>
    </div>
  </section>
</body>
</html>
```